Harbor Ledger Funds Bus card and Logo

I need a logo design and Bus card design. The fund focuses on evaluating and investing in minerals (sub-surface rights) and real estate.

Harbor ledger refers to a book of knowledge that each plebe gets when entering the Kelmont Marine Academy (my alma mater)

Target Market(s)

Investors and financial advisors

Contact Information for Business Card

Simple - perhaps a logo with a theme on book of knowledge

Logo Text

Ex Scientia Imperium

Font styles to use
Serif
Sans Serif

Colors

Designer to choose colors to be used in the design.

Requirements
Must have
• memorable logo that is relatively simple

```html
<!DOCTYPE html>
<html lang="en">
<head>
<meta charset="utf-8">
<title>Harbor Ledger Funds – Business Card</title>
<link rel="stylesheet" href="https://fonts.googleapis.com/css2?family=Arimo:wght@400;700&display=swap">
<style>
  :root {
    --page-bg: #d9d6d1;
    --card-frost-top: #f3f2f0;
    --card-frost-bottom: #dcdad8;
    --navy-deep: #0b1c45;
    --navy-mid: #173a7a;
    --navy-light: #2b5597;
    --accent-blue: #3d8fd0;
    --brand-ink: #101c3f;
    --contact-text: #eef2fa;
  }
  * { margin: 0; padding: 0; box-sizing: border-box; }
  html, body {
    width: 970px; height: 1200px; overflow: hidden;
    background: var(--page-bg);
  }
  .canvas { position: relative; width: 970px; height: 1200px; }
  .card {
    position: absolute; left: 175px; top: 60px;
    width: 620px; height: 1080px;
    border-radius: 36px; overflow: hidden;
    background: linear-gradient(180deg, var(--card-frost-top), var(--card-frost-bottom));
    box-shadow: 0 10px 30px rgba(0,0,0,.18);
  }
  .card-band { position: absolute; inset: 0; width: 620px; height: 1080px; }
  .brand {
    position: absolute; left: 180px; top: 110px; width: 420px;
    display: flex; flex-direction: column; align-items: center;
    color: var(--brand-ink);
    font-family: "Arimo", sans-serif; font-weight: 700;
    text-align: center;
  }
  .brand-mark {
    width: 120px; height: 120px; border-radius: 50%;
    background: var(--navy-mid);
    margin-bottom: 44px;
  }
  .brand-name { font-size: 40px; letter-spacing: 1px; line-height: 1.1; }
  .brand-sub { font-size: 24px; letter-spacing: 5px; line-height: 1.1; margin-top: 10px; }
  .contact {
    position: absolute; left: 42px; top: 712px;
    color: var(--contact-text); font-family: "Arimo", sans-serif;
  }
  .contact-name { font-size: 34px; font-weight: 700; line-height: 1.1; }
  .contact-role { font-size: 23px; margin-top: 4px; }
  .contact-address { font-size: 24px; line-height: 1.4; margin-top: 24px; }
  .contact-lines { list-style: none; margin-top: 18px; }
  .contact-lines li {
    display: flex; align-items: center; gap: 14px;
    font-size: 24px; height: 39px;
  }
  .contact-icon { width: 32px; height: 32px; flex: none; }
</style>
</head>
<body>
<div class="canvas">
  <div class="card">
    <svg class="card-band" viewBox="0 0 620 1080" aria-hidden="true">
      <defs>
        <linearGradient id="band-fill" x1="0" y1="0" x2="0.4" y2="1">
          <stop offset="0" stop-color="var(--navy-mid)"/>
          <stop offset="0.45" stop-color="var(--navy-deep)"/>
          <stop offset="1" stop-color="var(--navy-light)"/>
        </linearGradient>
      </defs>
      <path d="M0 0 H152 C70 30 20 130 100 290 L368 667 C440 770 520 860 441 1080 H0 Z" fill="url(#band-fill)"/>
      <path d="M152 0 C70 30 20 130 100 290" fill="none" stroke="var(--accent-blue)" stroke-width="4"/>
      <path d="M392 700 C470 790 535 880 470 1080" fill="none" stroke="var(--accent-blue)" stroke-width="4"/>
    </svg>

    <div class="brand">
      <div class="brand-mark"></div>
      <div class="brand-name">HARBOR LEDGER</div>
      <div class="brand-sub">FUNDS LLC</div>
    </div>

    <div class="contact">
      <div class="contact-name">Jordan Hale</div>
      <div class="contact-role">Manager</div>
      <div class="contact-address">PO BOX 480, Quay Road<br>Suite 2, Tidewater Bay</div>
      <ul class="contact-lines">
        <li>
          <svg class="contact-icon" viewBox="0 0 32 32" aria-hidden="true">
            <circle cx="16" cy="16" r="14" fill="none" stroke="currentColor" stroke-width="2"/>
            <path d="M11 9 l3 -1 2 5 -2 1.5 c1 2.5 2.5 4 5 5 l1.5 -2 5 2 -1 3 c-7 0 -13.5 -6.5 -13.5 -13.5z" fill="currentColor" transform="translate(-1 0)"/>
          </svg>
          555.210.4470
        </li>
        <li>
          <svg class="contact-icon" viewBox="0 0 32 32" aria-hidden="true">
            <circle cx="16" cy="16" r="14" fill="none" stroke="currentColor" stroke-width="2"/>
            <rect x="9" y="11" width="14" height="10" fill="none" stroke="currentColor" stroke-width="1.8"/>
            <path d="M9 11 l7 6 7 -6" fill="none" stroke="currentColor" stroke-width="1.8"/>
          </svg>
          info@harborledger.com
        </li>
        <li>
          <svg class="contact-icon" viewBox="0 0 32 32" aria-hidden="true">
            <circle cx="16" cy="16" r="14" fill="none" stroke="currentColor" stroke-width="2"/>
            <circle cx="16" cy="16" r="8" fill="none" stroke="currentColor" stroke-width="1.6"/>
            <ellipse cx="16" cy="16" rx="3.5" ry="8" fill="none" stroke="currentColor" stroke-width="1.4"/>
            <path d="M8 16 H24" stroke="currentColor" stroke-width="1.4"/>
          </svg>
          www.harborledger.com
        </li>
      </ul>
    </div>
  </div>
</div>
</body>
</html>
```